Web Design job - Condo Debts Collection Business needs a Web Design

I need a site for a client, who works with condo debts collection, and ensure all revenues provided by condo fees will be always available to the building manager of condo on a specific date, regardless of defaults.
I have the visual identity (logo, slogan and colors) of the company, and some requirements on layout (kind of slider, menu options, phone number on a noble position, etc) - maybe I can do a sketch, but I like the idea of give some freedom to designer.

*** PLEASE, we have no interest in templates. We want something new***

Target Market(s)

I have two targets for this design: - Condominium's building manager. This target is looking for a solution to overdue debts on it's condo. - Residents on condominiums. This target wants to live in a better place, where their neighbors pay their condominium fees on time.

Number of Pages Required

1 page

Requirements
Must have
• - Slider with title, some short text related, a nice image (I prefer happy and/or peaceful family, people doing business, happy friends, and so on).
• - I have a special attention to menu. I'm looking for one I can have a nice effect, more elegant, charming, kind of innovative.
• - Phone number on the top (or clearly visible).
• - Member log in area or icon on the top (or clearly visible).
• - News/articles area.
• - Modern fonts, with good quality, sans-serif on areas where reading is more intensive (prefer Google web-fonts).
• - Colors specified on attached files.
Nice to have
• - Clear background color, cause it's better to read larger texts (like articles). Dark backgrounds makes reading difficult.
• - A site with effects (like shadows, lines, curves, gradients, lights) is usually pretty.
• - I pay attention on beautiful footers.
Should not have
• - Images with a lot of money (I don't sell richness, I sell tranquility, peace, harmony, safety).
• - Poor menu.

```html
<!DOCTYPE html>
<html lang="en">
<head>
<meta charset="utf-8">
<title>Quorum – Condo Debts Collection</title>
<link href="https://fonts.googleapis.com/css2?family=Poppins:wght@400;500;600&family=Open+Sans:wght@400;600&family=Roboto+Condensed:wght@700&display=swap" rel="stylesheet">
<style>
:root{
  --gold:#e3a11b;
  --gold-light:#f0c04a;
  --navy:#1b2a3d;
  --navy-deep:#12202f;
  --ink:#1c1c1c;
  --text:#555;
  --white:#fff;
  --line:#e6e6e6;
}
*{box-sizing:border-box;margin:0;padding:0}
html,body{width:1200px;height:4147px;overflow:hidden}
body{font-family:"Open Sans",Arial,sans-serif;color:var(--text);background:var(--white);position:relative}
.abs{position:absolute}
h2.section-title{font-family:"Poppins",Arial,sans-serif;font-weight:500;font-size:38px;color:var(--ink);text-align:center;position:absolute;left:0;width:1200px}
p.section-sub{font-family:"Poppins",Arial,sans-serif;font-size:21px;color:#333;text-align:center;position:absolute;left:0;width:1200px}

/* header */
.topbar{position:absolute;left:0;top:0;width:1200px;height:90px}
.brand{position:absolute;left:90px;top:20px;display:flex;align-items:center;gap:14px;font-family:"Poppins",Arial,sans-serif;font-weight:600;font-size:44px;color:var(--ink)}
.brand-mark{width:40px;height:40px;background:var(--gold)}
.phone{position:absolute;left:748px;top:24px;font-family:"Poppins",Arial,sans-serif;font-size:22px;color:#444;display:flex;align-items:center;gap:8px;white-space:nowrap}
.login{position:absolute;left:970px;top:24px;width:140px;height:32px;background:var(--ink);color:var(--white);font-size:16px;text-align:center;line-height:32px;border-right:6px solid var(--gold)}
.nav-band{position:absolute;left:0;top:72px}
.nav{position:absolute;top:108px;left:492px;font-family:"Poppins",Arial,sans-serif;font-size:19px;color:var(--white)}
.nav a{color:var(--white);text-decoration:none;position:absolute;white-space:nowrap}
.nav a.active{color:var(--ink)}

/* hero */
.hero-photo{position:absolute;left:0;top:152px;width:1200px;height:620px;background:linear-gradient(100deg,#1c2a44 0%,#24365a 45%,#6f7480 70%,#c9b79a 100%)}
.hero-title{position:absolute;left:88px;top:365px;font-family:"Roboto Condensed",Arial,sans-serif;font-weight:700;font-size:54px;color:var(--white);letter-spacing:1px}
.hero-sub{position:absolute;left:88px;top:430px;font-family:"Roboto Condensed",Arial,sans-serif;font-weight:700;font-size:31px;color:var(--white)}
.dots{position:absolute;left:1158px;top:380px}
.dots span{display:block;width:9px;height:9px;border-radius:50%;background:var(--gold);margin-bottom:14px;opacity:.8}

/* services */
.service{position:absolute;width:300px;text-align:center}
.service .icon{margin:0 auto;width:130px;height:130px;position:relative}
.service h3{font-family:"Poppins",Arial,sans-serif;font-weight:500;font-size:23px;color:var(--ink);margin-top:20px}
.service p{font-size:15px;line-height:23px;color:#666;margin-top:12px}
.service .more{margin-top:12px}

/* about */
.about-bg{position:absolute;left:0;top:1369px;width:1200px;height:540px;background:linear-gradient(180deg,#232323,#1a1a1a)}
.about-title{color:var(--white)!important}
.about-text{position:absolute;left:130px;top:1558px;width:940px;text-align:center;color:var(--white);font-size:15px;line-height:28px}
.btn-light{position:absolute;background:var(--white);color:var(--ink);border-radius:22px;text-align:center;font-family:"Poppins",Arial,sans-serif;font-size:17px}

/* what we do */
.feature{position:absolute;width:330px}
.feature h4{font-family:"Poppins",Arial,sans-serif;font-weight:500;font-size:21px;color:var(--ink)}
.feature p{font-size:14px;line-height:22px;color:#555;margin-top:6px}
.feature.right{text-align:right}
.hub{position:absolute;left:428px;top:2123px;width:344px;height:344px;border-radius:50%;background:var(--white);box-shadow:0 0 30px rgba(0,0,0,.22);display:flex;align-items:center;justify-content:center;font-family:"Poppins",Arial,sans-serif;font-weight:600;font-size:48px;color:var(--gold)}

/* contact */
.contact-bg{position:absolute;left:0;top:2558px;width:1200px;height:565px;background:linear-gradient(180deg,#1a2a3e,#13202f)}
.field{position:absolute;border:1.5px solid #c9ced6;border-radius:4px;color:var(--white);font-size:18px;padding-left:20px;display:flex;align-items:center}

/* news */
.news-card{position:absolute;width:318px}
.news-photo{width:318px;height:196px;border:4px solid #eee;position:relative}
.news-date{position:absolute;left:6px;top:6px;width:52px;text-align:center;color:var(--white);font-size:13px}
.news-date .d{background:var(--gold);padding:4px 0 2px;font-size:17px;line-height:20px}
.news-date .d small{display:block;font-size:9px;line-height:10px}
.news-date .y{background:rgba(60,60,60,.85);padding:5px 0;font-size:13px}
.news-card h4{font-family:"Open Sans",Arial,sans-serif;font-weight:400;font-size:19px;color:var(--ink);margin-top:18px}
.news-card p{font-size:13.5px;line-height:22px;color:#444;margin-top:8px}
.news-card .read{font-size:13px;color:var(--gold);margin-top:10px}

/* footer */
.footer-bg{position:absolute;left:0;top:3843px;width:1200px;height:304px;background:#0b0b0b}
.foot-brand{position:absolute;left:98px;top:3946px;display:flex;align-items:center;gap:10px;font-family:"Poppins",Arial,sans-serif;font-weight:600;font-size:34px;color:var(--white)}
.foot-brand .brand-mark{width:30px;height:30px}
.foot-col{position:absolute;color:var(--white)}
.foot-col h5{font-family:"Open Sans",Arial,sans-serif;font-weight:400;font-size:15px;letter-spacing:.5px}
.foot-col ul{list-style:none;margin-top:14px}
.foot-col li{font-size:12.5px;line-height:23px}
.foot-col li::before{content:"›";color:var(--white);margin-right:8px}
.foot-col .row{display:flex;gap:12px;font-size:12.5px;line-height:21px;margin-top:12px}
.foot-col .row svg{flex:none;margin-top:3px}
.subscribe{display:flex;margin-top:14px}
.subscribe .in{width:146px;height:28px;background:var(--white);color:#888;font-size:11px;line-height:28px;padding-left:8px}
.subscribe .go{width:54px;height:28px;background:var(--gold);color:var(--white);font-size:12px;line-height:28px;text-align:center}
.copyright{position:absolute;left:0;top:4098px;width:1200px;text-align:center;color:var(--white);font-size:13px}
</style>
</head>
<body>

<!-- HEADER -->
<header class="topbar">
  <div class="brand"><span class="brand-mark"></span>Quorum</div>
  <div class="phone">
    <svg width="20" height="20" viewBox="0 0 24 24"><path d="M6.6 10.8a15 15 0 0 0 6.6 6.6l2.2-2.2c.3-.3.7-.4 1-.2 1.1.4 2.3.6 3.6.6.6 0 1 .4 1 1V20c0 .6-.4 1-1 1A17 17 0 0 1 3 4c0-.6.4-1 1-1h3.5c.6 0 1 .4 1 1 0 1.3.2 2.5.6 3.6.1.3 0 .7-.2 1z" fill="#e3a11b"/></svg>
    0800 555 0142
  </div>
  <div class="login">Member login</div>
</header>
<svg class="nav-band" width="1200" height="82" viewBox="0 0 1200 82">
  <polygon points="0,22 1200,0 1200,82 0,82" fill="#e3a11b"/>
  <polygon points="0,10 1200,0 1200,4 0,22" fill="#ffffff"/>
</svg>
<nav class="nav">
  <a class="active" style="left:0">Home</a>
  <a style="left:88px">About us</a>
  <a style="left:202px">Services</a>
  <a style="left:315px">Projects</a>
  <a style="left:429px">News</a>
  <a style="left:520px">Contact us</a>
</nav>

<!-- HERO -->
<div class="hero-photo" role="img" aria-label="Business team meeting around a desk with laptops, seen from above"></div>
<h1 class="hero-title">DEBTS COLLECTION</h1>
<p class="hero-sub">Neque porro quisquam dolorem</p>
<div class="dots"><span></span><span></span><span></span><span></span></div>
<svg class="abs" style="left:0;top:660px" width="1200" height="112" viewBox="0 0 1200 112">
  <polygon points="0,20 720,70 1200,70 1200,112 0,112" fill="#ffffff"/>
  <polygon points="0,20 1200,90 1200,100 0,112" fill="#e3a11b"/>
  <polygon points="0,112 1200,100 1200,112" fill="#ffffff"/>
</svg>

<!-- SERVICES -->
<h2 class="section-title" style="top:848px">Our Services</h2>
<p class="section-sub" style="top:898px">Neque porro quisquam est dolorem</p>

<div class="service" style="left:96px;top:990px">
  <div class="icon">
    <svg width="130" height="130" viewBox="0 0 130 130"><polygon points="8,0 122,0 65,64" fill="#f1dca8"/>
    <g fill="none" stroke="#222" stroke-width="3"><circle cx="65" cy="50" r="18"/><path d="M58 68h14v10H58z"/><path d="M20 70l14 30h14M110 70l-14 30H82M38 110h16M76 110h16"/><path d="M65 26v-8M44 34l-6-6M86 34l6-6"/></g></svg>
  </div>
  <h3>Neque porro</h3>
  <p>The point of using Lorem Ipsum is that it has a more-or-less normal distribution of letters, as opposed</p>
  <div class="more"><svg width="18" height="16" viewBox="0 0 18 16"><path d="M2 2l7 6 7-6M2 8l7 6 7-6" fill="none" stroke="#222" stroke-width="2.5"/></svg></div>
</div>
<div class="service" style="left:450px;top:990px">
  <div class="icon">
    <svg width="130" height="130" viewBox="0 0 130 130"><polygon points="8,0 122,0 65,64" fill="#f1dca8"/>
    <g fill="none" stroke="#222" stroke-width="3"><rect x="32" y="40" width="66" height="42" rx="4"/><path d="M22 92h86M40 92v20M90 92v20M50 56h30M50 66h20"/><circle cx="65" cy="28" r="8"/></g></svg>
  </div>
  <h3>Dolorem ipsum</h3>
  <p>The point of using Lorem Ipsum is that it has a more-or-less normal distribution of letters, as opposed</p>
  <div class="more"><svg width="18" height="16" viewBox="0 0 18 16"><path d="M2 2l7 6 7-6M2 8l7 6 7-6" fill="none" stroke="#222" stroke-width="2.5"/></svg></div>
</div>
<div class="service" style="left:798px;top:990px">
  <div class="icon">
    <svg width="130" height="130" viewBox="0 0 130 130"><polygon points="8,0 122,0 65,64" fill="#f1dca8"/>
    <g fill="none" stroke="#222" stroke-width="3"><rect x="24" y="36" width="82" height="56" rx="4"/><path d="M50 92l-6 18h42l-6-18M36 110h58"/><circle cx="50" cy="60" r="11"/><path d="M70 52h24M70 62h24M70 72h14"/></g></svg>
  </div>
  <h3>Porro quisquam</h3>
  <p>The point of using Lorem Ipsum is that it has a more-or-less normal distribution of letters, as opposed</p>
  <div class="more"><svg width="18" height="16" viewBox="0 0 18 16"><path d="M2 2l7 6 7-6M2 8l7 6 7-6" fill="none" stroke="#222" stroke-width="2.5"/></svg></div>
</div>

<!-- ABOUT -->
<div class="about-bg" role="img" aria-label="Dark office background photo"></div>
<svg class="abs" style="left:0;top:1369px" width="1200" height="70" viewBox="0 0 1200 70">
  <polygon points="0,0 1200,0 1200,0 0,28" fill="#ffffff"/>
  <polygon points="640,40 1200,0 1200,22" fill="#e3a11b"/>
</svg>
<h2 class="section-title about-title" style="top:1496px">About us</h2>
<p class="about-text">It is a long established fact that a reader will be distracted by the readable content of a page when looking at its layout. The point of using Lorem Ipsum is that it has a more-or-less normal distribution of letters, as opposed to using 'Content here, content here', making it look like readable English. Many desktop publishing packages and web page editors now use Lorem Ipsum as their default model text, and a search for 'lorem ipsum' will uncover many web sites still in their infancy The point of using Lorem Ipsum is that it has a more-or-less normal distribution of letters, as opposed to using</p>
<div class="btn-light" style="left:531px;top:1748px;width:138px;height:40px;line-height:40px">Read More</div>
<svg class="abs" style="left:0;top:1810px" width="1200" height="100" viewBox="0 0 1200 100">
  <polygon points="0,40 1200,0 1200,100 0,100" fill="#ffffff"/>
  <polygon points="0,40 560,22 0,96" fill="#e3a11b"/>
</svg>

<!-- WHAT WE DO -->
<h2 class="section-title" style="top:1976px">What We Do</h2>
<p class="section-sub" style="top:2030px">Neque porro quisquam est qui dolorem</p>

<svg class="abs" style="left:124px;top:2160px" width="52" height="42" viewBox="0 0 52 42"><g fill="none" stroke="#e3a11b" stroke-width="2"><rect x="2" y="2" width="48" height="30"/><path d="M18 40h16M26 32v8"/></g></svg>
<div class="feature" style="left:188px;top:2154px"><h4>Neque porro</h4><p>Duis aute irure dolor<br>in reprehenderit in voluptate.<br>Excepteur sint occaecat.</p></div>

<svg class="abs" style="left:132px;top:2318px" width="30" height="52" viewBox="0 0 30 52"><g fill="none" stroke="#e3a11b" stroke-width="2"><rect x="2" y="2" width="26" height="48" rx="4"/><path d="M11 42h8"/></g></svg>
<div class="feature" style="left:188px;top:2314px"><h4>Quisquam est</h4><p>Duis aute irure dolor<br>in reprehenderit in voluptate.<br>Excepteur sint occaecat.</p></div>

<div class="hub">Quorum</div>

<div class="feature right" style="left:682px;top:2160px"><h4>Dolorem ipsum</h4><p>Duis aute irure dolor<br>in reprehenderit in voluptate.<br>Excepteur sint occaecat.</p></div>
<svg class="abs" style="left:1026px;top:2166px" width="48" height="48" viewBox="0 0 48 48"><g fill="none" stroke="#e3a11b" stroke-width="2"><circle cx="10" cy="24" r="7"/><circle cx="38" cy="9" r="7"/><circle cx="38" cy="39" r="7"/><path d="M16 21l16-9M16 27l16 9"/></g></svg>

<div class="feature right" style="left:682px;top:2314px"><h4>porro quisquam</h4><p>Duis aute irure dolor<br>in reprehenderit in voluptate.<br>Excepteur sint occaecat.</p></div>
<svg class="abs" style="left:1030px;top:2318px" width="40" height="50" viewBox="0 0 40 50"><g fill="none" stroke="#e3a11b" stroke-width="2"><path d="M10 2h20l8 8v30H10z"/><path d="M2 12v36h28"/></g></svg>

<!-- CONTACT -->
<div class="contact-bg" role="img" aria-label="Dark navy office scene background"></div>
<svg class="abs" style="left:0;top:2540px" width="1200" height="120" viewBox="0 0 1200 120">
  <polygon points="0,18 1200,18 1200,20 0,120" fill="#ffffff"/>
  <polygon points="0,18 700,18 0,80" fill="#e3a11b"/>
</svg>
<h2 class="section-title" style="top:2700px;color:#fff">Contact us</h2>
<div class="field" style="left:218px;top:2793px;width:371px;height:55px">Name</div>
<div class="field" style="left:606px;top:2793px;width:376px;height:55px">Email id</div>
<div class="field" style="left:218px;top:2875px;width:764px;height:56px">Message</div>
<div class="btn-light" style="left:866px;top:2953px;width:116px;height:38px;line-height:38px">Submit</div>
<svg class="abs" style="left:0;top:3000px" width="1200" height="125" viewBox="0 0 1200 125">
  <polygon points="0,125 1200,40 1200,125" fill="#ffffff"/>
  <polygon points="560,86 1200,0 1200,40" fill="#e3a11b"/>
  <polygon points="1200,40 560,86 1200,86" fill="#e3a11b"/>
  <polygon points="0,125 1200,86 1200,125" fill="#ffffff"/>
</svg>

<!-- NEWS -->
<h2 class="section-title" style="top:3206px">Latest News</h2>
<p class="section-sub" style="top:3260px">Neque porro quisquam est qui dolorem</p>

<article class="news-card" style="left:93px;top:3346px">
  <div class="news-photo" role="img" aria-label="Hands working with a calculator and papers" style="background:linear-gradient(120deg,#5b6f8a,#b9c3cf 60%,#e6e8ec)">
    <div class="news-date"><div class="d">02<small>JUN</small></div><div class="y">2018</div></div>
  </div>
  <h4>Dolorem ipsum quia dolor</h4>
  <p>It has survived not only five centuries, but also the leap into electronic typesetting,</p>
  <div class="read">Read More »</div>
</article>
<article class="news-card" style="left:445px;top:3346px">
  <div class="news-photo" role="img" aria-label="Person reviewing documents at an office desk" style="background:linear-gradient(120deg,#d9d6cf,#b7b2a8 50%,#8d9aa8)">
    <div class="news-date"><div class="d">02<small>JUN</small></div><div class="y">2018</div></div>
  </div>
  <h4>Porro quisquam est</h4>
  <p>It has survived not only five centuries, but also the leap into electronic typesetting, remaining</p>
  <div class="read">Read More »</div>
</article>
<article class="news-card" style="left:799px;top:3346px">
  <div class="news-photo" role="img" aria-label="Person checking household bills at a table" style="background:linear-gradient(120deg,#c8b59a,#e8ddd0 50%,#9fa8b3)">
    <div class="news-date"><div class="d">02<small>JUN</small></div><div class="y">2018</div></div>
  </div>
  <h4>Neque porro quisquam</h4>
  <p>It has survived not only five centuries, but also the leap into electronic typesetting, remaining</p>
  <div class="read">Read More »</div>
</article>

<!-- FOOTER -->
<svg class="abs" style="left:0;top:3770px" width="1200" height="80" viewBox="0 0 1200 80">
  <polygon points="0,0 1200,50 1200,80 0,80" fill="#0b0b0b"/>
  <polygon points="0,0 1200,50 1200,74 0,30" fill="#e3a11b"/>
</svg>
<div class="footer-bg"></div>
<div class="foot-brand"><span class="brand-mark"></span>Quorum</div>

<div class="foot-col" style="left:351px;top:3896px">
  <h5>INFORMATION</h5>
  <ul><li>Privacy Policy</li><li>Your Account</li><li>Advanced Search</li><li>Contact Us</li></ul>
</div>
<div class="foot-col" style="left:581px;top:3896px;width:240px">
  <h5>CONTACT US</h5>
  <div class="row"><svg width="12" height="16" viewBox="0 0 12 16"><path d="M6 0a6 6 0 0 0-6 6c0 4.5 6 10 6 10s6-5.5 6-10a6 6 0 0 0-6-6zm0 8.5A2.5 2.5 0 1 1 6 3.5a2.5 2.5 0 0 1 0 5z" fill="#e3a11b"/></svg><span>1200 Harbor Lane, Suite 4,<br>Fairview, FL 30000</span></div>
  <div class="row"><svg width="14" height="14" viewBox="0 0 24 24"><path d="M6.6 10.8a15 15 0 0 0 6.6 6.6l2.2-2.2c.3-.3.7-.4 1-.2 1.1.4 2.3.6 3.6.6.6 0 1 .4 1 1V20c0 .6-.4 1-1 1A17 17 0 0 1 3 4c0-.6.4-1 1-1h3.5c.6 0 1 .4 1 1 0 1.3.2 2.5.6 3.6.1.3 0 .7-.2 1z" fill="#e3a11b"/></svg><span>0151 555 0190</span></div>
  <div class="row"><svg width="14" height="12" viewBox="0 0 14 12"><rect width="14" height="12" fill="#e3a11b"/><path d="M0 0l7 6 7-6" fill="none" stroke="#0b0b0b" stroke-width="1.5"/></svg><span>info@quorumcondo.example</span></div>
</div>
<div class="foot-col" style="left:908px;top:3896px;width:210px">
  <h5>JOIN OUR MAILING LIST</h5>
  <p style="font-size:12.5px;line-height:20px;margin-top:14px">Your about us information would fit here nicely.</p>
  <div class="subscribe"><div class="in">Email address</div><div class="go">Submit</div></div>
</div>
<div class="abs" style="left:94px;top:4072px;width:1012px;height:1px;background:#2a2a2a"></div>
<p class="copyright">Copyright © 2018 All Rights Reserved</p>

</body>
</html>
```